BrivoNest Learning App for Children with Dyslexia

Project Description:

We are seeking a talented UI/UX designer to create engaging and intuitive designs for Brivonest, an innovative educational app designed to help children learn letters and words through a multisensory learning approach. The app aims to be particularly helpful for children with dyslexia, providing a supportive and interactive learning environment.

Key App Features & Design Requirements:

Account Creation Screen: Design a welcoming and straightforward sign-up page that allows users to register with their email or continue with Quarnix. The design should be clean, focusing on user-friendliness and accessibility, adhering to our terms of service and privacy policy.

Main Screen Design: The main screen should allocate at least 4/6 of its height to the interactive drawing area. It needs to display word prompts in both correct and scrambled orders and include options to "Show all Words," "Play all words," and a search function. The interface should be vibrant, engaging, and easy to navigate for children.

Profile Section: Create a user-friendly profile page that allows users to edit their profile image, name, username, email, links, and bio. The design should be clean and encourage user engagement.

BrivoTally Page: This section will display the user's learning progress, including rankings, a learning curve, and recently learned words. It should visually represent progress in a motivating and understandable way, suitable for a younger audience.

Visual and Auditory Feedback Implementation: Incorporate elements that support visual and auditory feedback, using dyslexia-friendly formats. This includes choosing appropriate colors, fonts, and auditory cues.

Accessibility and Customization Settings: Designs should include settings for adjusting visual contrast, font size, and the word list to accommodate individual preferences and needs.

Feel free to add more interactions and/or pages.

Design preferences:

Color Scheme: Use a bright, inviting color palette that stimulates learning and engagement without overwhelming the users.
Font Selection: Opt for fonts that are readable and accessible, particularly for users with dyslexia.
Icons and Graphics: Design custom icons and graphics that are cohesive with the app's theme and purpose. Illustrations should be simple, relatable, and supportive of the learning process.

Target Market(s)

Educational

Industry/Entity Type

Educational

Colors
0054AA
0677BA
7BADD7
CADEEF
E8F1F8
0094D4
00A9DD
6FCCEA
C7EBF8
E9F6FB

Requirements
Must have
• Educational app, a writing area, scoring and account management
Nice to have
• Statistics, Ranking Page, Settings and some nice visual features

```html
<!DOCTYPE html>
<html lang="en">
<head>
<meta charset="utf-8">
<title>BrivoNest Learning App – Main Screen</title>
<link href="https://fonts.googleapis.com/css2?family=Orbitron:wght@800&family=Roboto:wght@400;500;700&display=swap" rel="stylesheet">
<style>
  :root{
    --bg-top:#0f7bb0;
    --bg-bottom:#0b4a86;
    --white:#ffffff;
    --screen-bg:#cadeef;
    --canvas:#f7f7f7;
    --frame-line:#7badd7;
    --toolbar:#3a4456;
    --ink:#1b1f27;
    --muted:#b9bec6;
    --primary:#0054aa;
    --cyan:#34dcf0;
    --green:#8ee26a;
    --red:#f0505a;
    --undo:#00a9dd;
    --redo:#58c84a;
    --pill:#a9bfd6;
    --card:#ffffff;
  }
  *{box-sizing:border-box;margin:0;padding:0}
  html,body{width:715px;height:1200px;overflow:hidden}
  body{
    background:linear-gradient(180deg,var(--bg-top),var(--bg-bottom));
    font-family:"Roboto",sans-serif;
    position:relative;
  }
  .board-title{
    position:absolute;top:70px;left:0;width:715px;text-align:center;color:var(--white);
  }
  .board-title h1{
    font-family:"Orbitron",sans-serif;font-weight:800;font-size:31px;letter-spacing:3px;white-space:nowrap;
  }
  .board-title p{font-size:27px;font-weight:400;margin-top:10px}

  .screen-label{
    position:absolute;top:490px;height:400px;width:16px;
    writing-mode:vertical-rl;transform:rotate(180deg);
    color:var(--white);font-size:10px;font-weight:700;letter-spacing:4.5px;
    text-align:center;white-space:nowrap;line-height:16px;
  }
  .screen{
    position:absolute;top:250px;width:270px;height:640px;border-radius:38px;
    background:var(--screen-bg);overflow:hidden;
    box-shadow:0 0 0 6px #141a24,0 14px 30px rgba(0,0,0,.35);
  }
  .status-bar{position:absolute;top:18px;left:34px;right:28px;display:flex;justify-content:space-between;align-items:center;font-size:14px;font-weight:500;color:var(--ink)}
  .status-icons{display:flex;gap:5px;align-items:center}
  .top-row{position:absolute;top:46px;left:14px;right:14px;height:30px;display:flex;justify-content:space-between;align-items:center}
  .round-btn{width:30px;height:30px;border-radius:50%;background:var(--white);display:flex;align-items:center;justify-content:center}
  .points-pill{width:108px;height:28px;border-radius:14px;background:var(--pill);display:flex;align-items:center;justify-content:space-between;padding:0 14px 0 12px;font-size:13px;font-weight:700;color:var(--ink)}
  .drawing-area{
    position:absolute;top:108px;left:0;right:0;height:310px;background:var(--canvas);
    border-top:4px solid var(--frame-line);border-bottom:4px solid var(--frame-line);
    border-radius:18px;
  }
  .toolbar{
    position:absolute;top:96px;left:50%;transform:translateX(-50%);width:124px;height:32px;
    background:var(--toolbar);border-radius:0 0 14px 14px;display:flex;justify-content:space-around;align-items:center;padding:0 12px;z-index:2
  }
  .toolbar-ears{position:absolute;top:96px;left:50%;transform:translateX(-50%);width:184px;height:12px;background:var(--toolbar);border-radius:8px 8px 0 0}
  .placeholder{position:absolute;top:150px;width:100%;text-align:center;color:var(--muted);font-size:13px}
  .answer-ink{position:absolute;top:115px;left:55px;width:160px;height:70px;background:linear-gradient(90deg,#e6e6e6,#d8d8d8);border-radius:10px}
  .mode-switch{
    position:absolute;top:405px;left:50%;transform:translateX(-50%);width:160px;height:36px;border-radius:18px;
    background:var(--toolbar);display:flex;align-items:center;justify-content:space-between;padding:3px;z-index:2
  }
  .mode-chip{height:30px;border-radius:15px;display:flex;align-items:center;gap:8px;padding:0 10px;font-size:10px;font-weight:500;color:var(--ink);white-space:nowrap}
  .mode-switch.show .mode-chip.eye{background:var(--cyan);width:118px}
  .mode-switch.play .mode-chip.playing{background:var(--green);width:112px;justify-content:space-between;padding-right:4px}
  .mini-circle{width:20px;height:20px;border-radius:50%;display:flex;align-items:center;justify-content:center;flex:none}
  .word-grid{position:absolute;top:460px;left:16px;right:16px;display:grid;grid-template-columns:repeat(3,1fr);gap:12px 14px}
  .word-card{height:32px;background:var(--card);display:flex;align-items:center;justify-content:center;font-size:13px;font-weight:500;color:var(--ink);
    clip-path:polygon(0 0,100% 0,100% 70%,88% 100%,0 100%)}
  .view-results{position:absolute;top:566px;left:14px;right:14px;height:36px;border-radius:6px;background:var(--primary);color:var(--white);font-size:13px;font-weight:500;display:flex;align-items:center;justify-content:center}
  .home-indicator{position:absolute;bottom:10px;left:50%;transform:translateX(-50%);width:100px;height:4px;border-radius:2px;background:var(--white)}
</style>
</head>
<body>
  <header class="board-title">
    <h1>BRIVONEST LEARNING APP</h1>
    <p>for Children with Dyslexia</p>
  </header>

  <div class="screen-label" style="left:24px">MAIN SCREEN - SHOW ALL WORDS TAB</div>
  <section class="screen" style="left:60px" aria-label="Main screen, show all words tab">
    <div class="status-bar"><span>9:41</span>
      <span class="status-icons">
        <svg width="16" height="10"><rect x="0" y="7" width="3" height="3" fill="#1b1f27"/><rect x="4" y="5" width="3" height="5" fill="#1b1f27"/><rect x="8" y="3" width="3" height="7" fill="#1b1f27"/><rect x="12" y="0" width="3" height="10" fill="#1b1f27"/></svg>
        <svg width="14" height="10"><path d="M1 4a9 9 0 0 1 12 0M3.5 6.5a5 5 0 0 1 7 0" stroke="#1b1f27" stroke-width="1.6" fill="none"/><circle cx="7" cy="9" r="1.2" fill="#1b1f27"/></svg>
        <svg width="22" height="11"><rect x="0.5" y="0.5" width="19" height="10" rx="3" fill="none" stroke="#1b1f27"/><rect x="2" y="2" width="16" height="7" rx="2" fill="#1b1f27"/></svg>
      </span></div>
    <div class="top-row">
      <div class="round-btn"><svg width="12" height="12"><path d="M2 2l8 8M10 2l-8 8" stroke="#0054aa" stroke-width="2.2" stroke-linecap="round"/></svg></div>
      <div class="points-pill"><svg width="16" height="16"><circle cx="8" cy="9" r="6" fill="#f0505a"/><path d="M8 3l2-2" stroke="#58c84a" stroke-width="2"/></svg><span>16 pts.</span></div>
      <div class="round-btn"><svg width="14" height="14"><circle cx="6" cy="6" r="4" stroke="#0054aa" stroke-width="2" fill="none"/><path d="M9 9l4 4" stroke="#0054aa" stroke-width="2.4" stroke-linecap="round"/></svg></div>
    </div>
    <div class="drawing-area"><p class="placeholder">Draw your answer here</p></div>
    <div class="toolbar-ears"></div>
    <div class="toolbar">
      <svg width="16" height="16"><path d="M4 5a6 6 0 1 1-1 5" stroke="#00a9dd" stroke-width="2.2" fill="none" stroke-linecap="round"/><path d="M2 2v4h4" stroke="#00a9dd" stroke-width="2.2" fill="none"/></svg>
      <svg width="14" height="16"><rect x="2" y="5" width="10" height="10" rx="2" fill="#f0505a"/><rect x="0" y="2" width="14" height="2.5" rx="1" fill="#f0505a"/></svg>
      <svg width="16" height="16"><path d="M12 5a6 6 0 1 0 1 5" stroke="#58c84a" stroke-width="2.2" fill="none" stroke-linecap="round"/><path d="M14 2v4h-4" stroke="#58c84a" stroke-width="2.2" fill="none"/></svg>
    </div>
    <div class="mode-switch show">
      <div class="mode-chip eye"><svg width="18" height="12"><ellipse cx="9" cy="6" rx="8" ry="5" fill="#1b1f27"/><circle cx="9" cy="6" r="2.5" fill="#34dcf0"/></svg>Show all words</div>
      <div class="mini-circle" style="background:#8ee26a;margin-right:5px"><svg width="8" height="10"><path d="M1 1l6 4-6 4z" fill="#3a4456"/></svg></div>
    </div>
    <div class="word-grid">
      <div class="word-card">exile</div><div class="word-card">maroon</div><div class="word-card">clean</div>
      <div class="word-card">peace</div><div class="word-card">poets</div><div class="word-card">•••</div>
    </div>
    <div class="view-results">View results</div>
    <div class="home-indicator"></div>
  </section>

  <div class="screen-label" style="left:350px">MAIN SCREEN - PLAY ALL WORDS TAB</div>
  <section class="screen" style="left:386px" aria-label="Main screen, play all words tab">
    <div class="status-bar"><span>9:41</span>
      <span class="status-icons">
        <svg width="16" height="10"><rect x="0" y="7" width="3" height="3" fill="#1b1f27"/><rect x="4" y="5" width="3" height="5" fill="#1b1f27"/><rect x="8" y="3" width="3" height="7" fill="#1b1f27"/><rect x="12" y="0" width="3" height="10" fill="#1b1f27"/></svg>
        <svg width="14" height="10"><path d="M1 4a9 9 0 0 1 12 0M3.5 6.5a5 5 0 0 1 7 0" stroke="#1b1f27" stroke-width="1.6" fill="none"/><circle cx="7" cy="9" r="1.2" fill="#1b1f27"/></svg>
        <svg width="22" height="11"><rect x="0.5" y="0.5" width="19" height="10" rx="3" fill="none" stroke="#1b1f27"/><rect x="2" y="2" width="16" height="7" rx="2" fill="#1b1f27"/></svg>
      </span></div>
    <div class="top-row">
      <div class="round-btn"><svg width="12" height="12"><path d="M2 2l8 8M10 2l-8 8" stroke="#0054aa" stroke-width="2.2" stroke-linecap="round"/></svg></div>
      <div class="points-pill"><svg width="16" height="16"><circle cx="8" cy="9" r="6" fill="#f0505a"/><path d="M8 3l2-2" stroke="#58c84a" stroke-width="2"/></svg><span>16 pts.</span></div>
      <div class="round-btn"><svg width="14" height="14"><circle cx="6" cy="6" r="4" stroke="#0054aa" stroke-width="2" fill="none"/><path d="M9 9l4 4" stroke="#0054aa" stroke-width="2.4" stroke-linecap="round"/></svg></div>
    </div>
    <div class="drawing-area"><div class="answer-ink" role="img" aria-label="Handwritten answer: the word poets drawn in black ink"></div></div>
    <div class="toolbar-ears"></div>
    <div class="toolbar">
      <svg width="16" height="16"><path d="M4 5a6 6 0 1 1-1 5" stroke="#00a9dd" stroke-width="2.2" fill="none" stroke-linecap="round"/><path d="M2 2v4h4" stroke="#00a9dd" stroke-width="2.2" fill="none"/></svg>
      <svg width="14" height="16"><rect x="2" y="5" width="10" height="10" rx="2" fill="#f0505a"/><rect x="0" y="2" width="14" height="2.5" rx="1" fill="#f0505a"/></svg>
      <svg width="16" height="16"><path d="M12 5a6 6 0 1 0 1 5" stroke="#58c84a" stroke-width="2.2" fill="none" stroke-linecap="round"/><path d="M14 2v4h-4" stroke="#58c84a" stroke-width="2.2" fill="none"/></svg>
    </div>
    <div class="mode-switch play">
      <div class="mini-circle" style="margin-left:8px"><svg width="18" height="12"><ellipse cx="9" cy="6" rx="8" ry="5" fill="none" stroke="#34dcf0" stroke-width="2"/><circle cx="9" cy="6" r="2.3" fill="#34dcf0"/></svg></div>
      <div class="mode-chip playing">Play all words<span class="mini-circle" style="background:#1b1f27"><svg width="8" height="10"><path d="M1 1l6 4-6 4z" fill="#ffffff"/></svg></span></div>
    </div>
    <div class="word-grid">
      <div class="word-card">exile</div><div class="word-card">maroon</div><div class="word-card">clean</div>
      <div class="word-card">peace</div>
      <div class="word-card"><svg width="16" height="14"><path d="M1 5h3l4-4v12l-4-4H1z" fill="#0054aa"/><path d="M11 4a4 4 0 0 1 0 6" stroke="#0054aa" stroke-width="1.8" fill="none"/></svg></div>
      <div class="word-card">•••</div>
    </div>
    <div class="view-results">View results</div>
    <div class="home-indicator"></div>
  </section>
</body>
</html>
```